Family-owned company selling organic landscaping and gardening products needs new labels.

We need label designs initially for 6 products, the designs should be unique for each product but have common design elements. The products are organic and used in landscaping, gardening and horticulture industries. Products are used commercially and residentially. The products encourage root growth and soil health, so that could be featured in the label along with plants, trees, etc. We like the colors, the sunburst background and the art deco vibe in the label designs provided for inspiration, but we are open to other ideas as well. We are also providing a sample of current labels (bland, boring) for reference. We are also providing a copy of our new logo which we like but are open to suggestions. We would like to start with the label for our TERRA BLEND product.

```html
<!DOCTYPE html>
<html lang="en">
<head>
<meta charset="UTF-8">
<title>Terra Blend Label</title>
<link href="https://fonts.googleapis.com/css2?family=Archivo+Black&family=Fira+Sans+Condensed:wght@700;800&display=swap" rel="stylesheet">
<style>
  :root {
    --page-bg: #ececec;
    --gold-light: #f1c93a;
    --gold-mid: #dcaa22;
    --gold-deep: #c28c16;
    --soil-dark: #10130a;
    --ink: #1c1a17;
    --title-shadow: #3a2806;
    --white: #ffffff;
  }
  * { box-sizing: border-box; margin: 0; padding: 0; }
  html, body {
    width: 1088px; height: 1200px; overflow: hidden;
    background: var(--page-bg);
  }
  .label {
    position: absolute; left: 164px; top: 40px;
    width: 760px; height: 1120px; overflow: hidden;
    background: radial-gradient(circle at 50% 50%, var(--gold-light) 0%, var(--gold-mid) 50%, var(--gold-deep) 100%);
    font-family: "Fira Sans Condensed", "Arial Narrow", sans-serif;
  }
  .title {
    position: absolute; top: 60px; left: 0; right: 0;
    text-align: center;
    font-family: "Archivo Black", "Arial Black", sans-serif;
    font-size: 170px; line-height: 0.95; letter-spacing: -2px;
    color: var(--white);
    text-shadow: 5px 5px 0 var(--title-shadow), 8px 8px 0 var(--title-shadow);
  }
  .tagline-pill {
    position: absolute; top: 430px; left: 70px; width: 620px; height: 104px;
    border-radius: 52px; background: var(--ink); color: var(--white);
    display: flex; flex-direction: column; justify-content: center; align-items: center;
    font-size: 34px; font-weight: 700; line-height: 1.15;
  }
  .classification {
    position: absolute; top: 552px; left: 0; right: 0;
    text-align: center; color: var(--ink);
    font-size: 25px; font-weight: 800; line-height: 1.15; text-transform: uppercase;
  }
  .plant-art {
    position: absolute; top: 620px; left: 0; width: 760px; height: 300px;
    background: linear-gradient(180deg, rgba(120,90,15,0) 0%, rgba(110,85,20,0.22) 55%, rgba(70,60,20,0.45) 100%);
  }
  .soil-hill { position: absolute; left: 0; top: 740px; width: 760px; height: 380px; }
  .brand-badge {
    position: absolute; left: 50px; top: 900px; width: 176px; height: 176px;
    border-radius: 50%; background: var(--white); border: 5px solid var(--soil-dark);
    display: flex; align-items: center; justify-content: center;
    color: var(--soil-dark); font-size: 36px; font-weight: 800;
  }
  .pack-info {
    position: absolute; left: 270px; top: 950px;
    color: var(--white); font-size: 30px; font-weight: 700; line-height: 1.35;
  }
</style>
</head>
<body>
  <div class="label">
    <h1 class="title">TERRA<br>BLEND</h1>
    <div class="tagline-pill">
      <span>Endo-Ecto Mycorrhizal Inoculum</span>
      <span>For Most Plants</span>
    </div>
    <p class="classification">Auxiliary Soil and Plant Substance<br>Non Plant Food Ingredient</p>
    <div class="plant-art" role="img" aria-label="Line illustration of wildflowers and herbs growing along the soil"></div>
    <svg class="soil-hill" viewBox="0 0 760 380" preserveAspectRatio="none">
      <defs>
        <radialGradient id="soilGlow" cx="0.45" cy="0.6" r="0.7">
          <stop offset="0" stop-color="#3b4219"/>
          <stop offset="1" stop-color="#0e1108"/>
        </radialGradient>
      </defs>
      <path d="M0 150 C60 130 110 120 170 95 C220 80 260 110 310 95 C360 80 400 100 450 70 C500 40 540 60 600 30 C650 10 700 20 760 0 L760 380 L0 380 Z" fill="url(#soilGlow)"/>
    </svg>
    <div class="brand-badge">Rootwell</div>
    <div class="pack-info">
      <p>500 - 4 gram Terra Blend Paks</p>
      <p>Net Weight: 4.41 lbs (2.0 kg)</p>
    </div>
  </div>
</body>
</html>
```